Landscape Construction and Design Company

We are a landscape construction and design company from New Jersey. We design and install landscapes and hardscapes for residential properties. The name of the company is Belwick's Landscape and Design LLC. We specialize mostly in planting trees and stone work, some water features. We would like to see design themes that include a tree or trees and a stone walkway or wall. We like earth tone colors. We like traditional to modern designs.

Target Market(s)

Homeowners

Industry/Entity Type

Landscape

Contact Information for Business Card

Nature themed design, earth tone colors, space for company name, address, phone numbers, email and website address

Logo Text

No text

Font styles to use
Serif

Colors

Designer to choose colors to be used in the design.

Requirements
Must have
• A tree or trees, similar to the ones uploaded in my supporting images
Nice to have
• I like trees similar to those in my uploaded supporting images. I like artistic, nature theme, earth tone colors
Should not have
• Pictures of real landscapes, cartoon looking logo or objects

```html
<!DOCTYPE html>
<html lang="en">
<head>
<meta charset="utf-8">
<title>Belwick's Landscape and Design LLC – Business Card</title>
<link href="https://fonts.googleapis.com/css2?family=Lato:wght@400;700&display=swap" rel="stylesheet">
<style>
  :root {
    --leaf-green: #67a22d;
    --leaf-light: #8cc043;
    --bark-maroon: #7a2c2f;
    --paper: #ffffff;
    --ink: #2b2b2b;
    --rule: #9a9a9a;
    --backdrop: #ece8e1;
  }
  * { margin: 0; padding: 0; box-sizing: border-box; }
  html, body {
    width: 1200px; height: 900px; overflow: hidden;
    background: var(--backdrop);
    font-family: "Lato", Arial, sans-serif;
  }
  .card {
    position: absolute; left: 250px; width: 700px; height: 400px;
    box-shadow: 0 6px 18px rgba(0,0,0,0.15);
    overflow: hidden;
  }

  /* Front */
  .card-front { top: 30px; background: var(--leaf-green); }
  .front-mark {
    position: absolute; left: 110px; top: 110px;
    width: 180px; height: 180px; border-radius: 50%;
    background: var(--leaf-light);
  }
  .front-brand {
    position: absolute; left: 360px; top: 140px; width: 300px;
    text-align: center;
  }
  .wordmark {
    font-family: "Lato", Arial, sans-serif;
    font-weight: 400;
  }
  .front-brand .wordmark {
    color: var(--paper); font-size: 26px; line-height: 1.25;
  }
  .services {
    margin-top: 18px; font-weight: 700; font-size: 15px; line-height: 1.35;
    color: var(--paper);
  }

  /* Back */
  .card-back { top: 470px; background: var(--paper); }
  .back-brand {
    position: absolute; right: 40px; top: 40px;
    display: flex; align-items: center; gap: 14px;
  }
  .back-mark {
    width: 56px; height: 56px; border-radius: 50%; background: var(--leaf-light);
    flex: none;
  }
  .back-brand .wordmark {
    color: var(--leaf-green); font-size: 19px; line-height: 1.25; width: 190px;
  }
  .rule-top {
    position: absolute; left: 360px; right: 40px; top: 135px;
    height: 1px; background: var(--rule);
  }
  .holder { position: absolute; left: 44px; top: 208px; }
  .holder-name { color: var(--leaf-green); font-weight: 700; font-size: 24px; letter-spacing: 0.3px; }
  .holder-title { color: var(--ink); font-size: 18px; margin-top: 2px; }
  .rule-mid {
    position: absolute; left: 250px; right: 260px; top: 244px;
    height: 1px; background: var(--rule);
  }
  .address {
    position: absolute; right: 40px; top: 206px;
    text-align: right; color: var(--ink); font-size: 16px; line-height: 1.35;
    font-style: normal;
  }
  .contacts { position: absolute; left: 44px; top: 278px; list-style: none; }
  .contacts li {
    display: flex; align-items: center; gap: 10px;
    font-size: 18px; color: var(--ink); line-height: 1.45;
  }
  .contacts svg { width: 16px; height: 16px; fill: var(--leaf-green); flex: none; }
  .band {
    position: absolute; left: 0; right: 0; bottom: 0; height: 22px;
    display: flex;
  }
  .band-green { flex: 58; background: var(--leaf-green); }
  .band-maroon { flex: 42; background: var(--bark-maroon); }
</style>
</head>
<body>
  <section class="card card-front">
    <div class="front-mark" aria-hidden="true"></div>
    <div class="front-brand">
      <p class="wordmark">Belwick's Landscape and Design LLC</p>
      <p class="services">PLANTING TREES | STONE WORK<br>WATER FEATURES</p>
    </div>
  </section>

  <section class="card card-back">
    <div class="back-brand">
      <div class="back-mark" aria-hidden="true"></div>
      <p class="wordmark">Belwick's Landscape and Design LLC</p>
    </div>
    <div class="rule-top"></div>

    <div class="holder">
      <p class="holder-name">DANIEL HARPER</p>
      <p class="holder-title">Managing Director</p>
    </div>
    <div class="rule-mid"></div>

    <address class="address">
      421, Address line here<br>Country Name,45452
    </address>

    <ul class="contacts">
      <li>
        <svg viewBox="0 0 16 16" aria-hidden="true"><path d="M3 1h3l1.5 4-2 1.3a9 9 0 0 0 4.2 4.2L11 8.5l4 1.5v3a2 2 0 0 1-2 2C6.4 15 1 9.6 1 3a2 2 0 0 1 2-2z"/></svg>
        444 555 0192
      </li>
      <li>
        <svg viewBox="0 0 16 16" aria-hidden="true"><path d="M1 3h14v10H1z M1.5 3.5 8 9l6.5-5.5" stroke="#fff" stroke-width="1.2"/></svg>
        info@youremail.com
      </li>
      <li>
        <svg viewBox="0 0 16 16" aria-hidden="true"><circle cx="8" cy="8" r="7"/><path d="M1 8h14M8 1c2.5 2.5 2.5 11.5 0 14M8 1c-2.5 2.5-2.5 11.5 0 14" stroke="#fff" stroke-width="1" fill="none"/></svg>
        www.websitename.com
      </li>
    </ul>

    <div class="band"><span class="band-green"></span><span class="band-maroon"></span></div>
  </section>
</body>
</html>
```